A multi-page brochure that explains our firm ,KVL Wealth Management

We have a current brochure attached but it is a compilation of several items combined into one. We would like this to have the same content but be one complete theme. We are a financial planning form so it needs to have a level of professionalism but also a comfortable approach for clients and showing that was have a lot of resources and experience. We cater mostly to the 55-60+ age community.

We need the front page picture changed. lake themed would be great, like our website www.TheMoskaHouse.com
Just to be clear we use KVL Wealth Management now as our company name. Parent company name is The Moska House LLC. I attached the current mock brochure and our new logos.
Our logo colors are:
KVL WM Logo Colors:

Blue:
HEX: #0f75bc
RGB: rgba(15,117,188,255)

Grey:
HEX: #6d6e71
RGB: rgba(109,110,113,255)

Target Market(s)

High-level individuals that are looking for financial guidance who are 40 years old and up

Industry/Entity Type

Wealth Management

Requirements
Must have
• Clean and crisp
Nice to have
• https://www.bramblestoneplanners.com/wealth-management-brochure , this is a sample we like

```html
<!DOCTYPE html>
<html lang="en">
<head>
<meta charset="utf-8">
<title>KVL Wealth Management – Brochure</title>
<link href="https://fonts.googleapis.com/css2?family=Cinzel:wght@600;700&family=Open+Sans:ital,wght@0,400;0,600;1,400&display=swap" rel="stylesheet">
<style>
:root{
  --brand-blue:#0f75bc;
  --brand-grey:#6d6e71;
  --backdrop:#6c6d71;
  --paper:#ffffff;
  --body-text:#55565a;
  --sky-top:#cfe6f5;
  --sky-low:#e9f3f7;
  --lake:#3fa6b4;
  --rock:#9c8f7a;
}
*{box-sizing:border-box;margin:0;padding:0}
html,body{width:1200px;height:544px;overflow:hidden;background:var(--backdrop)}
body{position:relative;font-family:"Open Sans",Arial,sans-serif;color:var(--body-text)}
.page{position:absolute;top:37px;width:355px;height:459px;background:var(--paper);overflow:hidden;box-shadow:0 1px 4px rgba(0,0,0,.25)}
.page--cover{left:42px}
.page--partner{left:423px}
.page--firm{left:805px}

/* cover */
.cover-photo{position:absolute;left:0;top:0;width:355px;height:300px;
  background:linear-gradient(180deg,var(--sky-top) 0%,var(--sky-low) 38%,#8fb9c4 52%,var(--lake) 68%,var(--rock) 92%)}
.cover-wave{position:absolute;left:0;top:222px;width:355px;height:80px}
.cover-panel{position:absolute;left:0;top:300px;width:355px;height:159px;background:var(--brand-blue)}
.cover-brand{position:absolute;left:0;top:34px;width:355px;text-align:center;font-family:"Cinzel",Georgia,serif;font-weight:700;color:var(--brand-blue);font-size:25px;line-height:27px;letter-spacing:.5px}
.cover-title{position:absolute;left:25px;top:318px;width:290px;font-family:"Cinzel",Georgia,serif;font-weight:700;color:#fff;font-size:20px;line-height:22.5px}
.cover-rule{position:absolute;left:25px;top:393px;width:72px;height:2px;background:#fff}
.cover-lead{position:absolute;left:25px;top:403px;width:290px;color:#fff;font-size:10.4px;line-height:14px}

/* inner pages */
.page-head{position:absolute;left:0;top:0;width:355px;height:50px}
.page-head__tab{position:absolute;left:0;top:15px;width:4px;height:20px;background:var(--brand-grey)}
.page-head__title{position:absolute;left:16px;top:16px;font-family:"Cinzel",Georgia,serif;font-weight:700;color:var(--brand-blue);font-size:14.5px;letter-spacing:.3px;white-space:nowrap}
.page-head__title .muted{color:var(--brand-grey)}
.page-head__brand{position:absolute;right:18px;top:12px;font-family:"Cinzel",Georgia,serif;font-weight:700;color:var(--brand-blue);font-size:17px}
.page-foot{position:absolute;left:0;bottom:0;width:355px;height:23px;background:var(--brand-blue);color:#fff;font-size:6.8px;display:flex;align-items:center;justify-content:space-between;padding:0 17px}
.page-foot__num b{font-size:9px;font-weight:600}

.team-photo{position:absolute;left:0;top:50px;width:355px;height:182px;background:linear-gradient(135deg,#d9d6cf 0%,#b9a995 40%,#6f86a2 60%,#e4e4e2 100%)}
.bullets{position:absolute;top:257px;width:150px;list-style:none;font-size:7px;line-height:12.2px}
.bullets--left{left:19px}
.bullets--right{left:186px}
.bullets li{position:relative;padding-left:8.5px;margin-bottom:12.3px}
.bullets li::before{content:"";position:absolute;left:0;top:4px;width:4px;height:4px;border-radius:50%;background:var(--brand-blue)}

.intro{position:absolute;left:18px;top:50px;width:322px;font-size:6.9px;line-height:10.4px}
.principles{position:absolute;left:20px;top:90px;width:320px;list-style:none}
.principle{position:relative;height:43px;padding-left:44px}
.principle__icon{position:absolute;left:0;top:1px;width:30px;height:30px;border-radius:50%;background:var(--brand-blue);display:flex;align-items:center;justify-content:center}
.principle__icon--grey{background:var(--brand-grey)}
.principle h3{font-family:"Cinzel",Georgia,serif;font-weight:700;color:var(--brand-grey);font-size:9.5px;line-height:12px;margin-bottom:2px}
.principle p{font-size:6.2px;line-height:8.4px;width:270px}
.firm-body{position:absolute;left:20px;top:224px;width:320px;font-size:6.6px;line-height:10.9px}
.firm-note{position:absolute;left:20px;top:278px;width:320px;font-size:6.6px;line-height:10.9px;font-style:italic}
.location{position:absolute;top:309px;width:154px;height:98px}
.location--mpls{left:18px;background:linear-gradient(180deg,#4f8fd8 0%,#8fb6e2 40%,#5e6f7c 62%,#3d5c78 100%)}
.location--sf{left:183px;background:linear-gradient(180deg,#5a9ad6 0%,#a9c4d8 35%,#b88c70 55%,#5d8a4a 80%,#3c6b86 100%)}
.location__label{position:absolute;top:398px;width:128px;height:17px;color:#fff;font-size:8px;text-align:center;line-height:17px}
.location__label--mpls{left:30px;background:var(--brand-blue)}
.location__label--sf{left:195px;background:var(--brand-grey)}
</style>
</head>
<body>

<section class="page page--cover">
  <div class="cover-photo" role="img" aria-label="Photo of a calm mountain lake with a wooden pier and rocky shore"></div>
  <svg class="cover-wave" viewBox="0 0 355 80" preserveAspectRatio="none" aria-hidden="true">
    <path d="M0 70 C90 30 170 50 240 52 C300 54 335 36 355 24 L355 80 L0 80 Z" fill="#6d6e71"/>
    <path d="M0 62 C90 22 170 40 240 44 C300 48 335 28 355 16 L355 32 C330 48 300 62 240 62 C170 62 90 44 0 76 Z" fill="#ffffff"/>
    <path d="M0 80 C90 48 170 70 240 72 C300 74 335 56 355 44 L355 80 Z" fill="#0f75bc"/>
  </svg>
  <div class="cover-panel"></div>
  <div class="cover-brand">KVL Wealth<br>Management</div>
  <h1 class="cover-title">Wealth Management Focused on Your Needs and Vision</h1>
  <div class="cover-rule"></div>
  <p class="cover-lead">Understanding your unique needs and vision for the future is the starting point for our relationship.</p>
</section>

<section class="page page--partner">
  <header class="page-head">
    <span class="page-head__tab"></span>
    <h2 class="page-head__title">Partner <span class="muted">with a</span> Specialist</h2>
    <span class="page-head__brand">KVL</span>
  </header>
  <div class="team-photo" role="img" aria-label="Photo of an advisor reviewing a plan on a laptop with a couple at a table"></div>
  <ul class="bullets bullets--left">
    <li>Understanding your unique needs and vision for the future is the starting point for our relationship.</li>
    <li>Together, we'll assess where you are financially and where you want to be.</li>
    <li>Next, we'll create a comprehensive wealth management plan that addresses your immediate and long-term goals.</li>
    <li>What about the unpredictable? We'll plan for the changes that may be ahead, too.</li>
  </ul>
  <ul class="bullets bullets--right">
    <li>Exploring the topics of interest presented in this brochure will give you an idea of the depth and breadth of our services.</li>
    <li>Rest assured that we'll partner with you throughout the planning process, always circling back to this fundamental question:</li>
    <li>what's right for you and your loved ones?</li>
  </ul>
  <footer class="page-foot"><span>Copyright @ 2026 KVL Wealth Management</span><span class="page-foot__num">Page Number: <b>02</b></span></footer>
</section>

<section class="page page--firm">
  <header class="page-head">
    <span class="page-head__tab"></span>
    <h2 class="page-head__title">Our <span class="muted">Firm</span></h2>
    <span class="page-head__brand">KVL</span>
  </header>
  <p class="intro">The Moska House LLC, established in 1987, is an independent, full-service, financial consulting firm. As we search the marketplace for innovative, strategic solutions, The Moska House is guided by the following principles:</p>
  <ul class="principles">
    <li class="principle">
      <span class="principle__icon"><svg width="16" height="16" viewBox="0 0 16 16" aria-hidden="true"><path d="M3 8.5l3 3 7-7" stroke="#fff" stroke-width="2" fill="none" stroke-linecap="round" stroke-linejoin="round"/></svg></span>
      <h3>Service</h3>
      <p>We seek to anticipate your needs and exceed your expectations in every aspect of our partnership.</p>
    </li>
    <li class="principle">
      <span class="principle__icon principle__icon--grey"><svg width="16" height="16" viewBox="0 0 16 16" aria-hidden="true"><rect x="3" y="2" width="10" height="12" rx="1" stroke="#fff" stroke-width="1.4" fill="none"/><path d="M5.5 6h5M5.5 8.5h5M5.5 11h3" stroke="#fff" stroke-width="1.2"/></svg></span>
      <h3>Planning</h3>
      <p>We collaborate with you by listening, asking questions, educating and helping you make informed decisions to skillfully implement appropriate, effective financial strategies.</p>
    </li>
    <li class="principle">
      <span class="principle__icon"><svg width="16" height="16" viewBox="0 0 16 16" aria-hidden="true"><path d="M8 2l5 2v4c0 3-2.2 5-5 6-2.8-1-5-3-5-6V4z" stroke="#fff" stroke-width="1.4" fill="none" stroke-linejoin="round"/></svg></span>
      <h3>Integrity</h3>
      <p>We build long-term client relationships and are proud of the integrity and sensitivity we exhibit when working with all our clients.</p>
    </li>
  </ul>
  <p class="firm-body">The Moska House has created an environment of objectivity and independence in which to provide independent guidance and access to the widest variety of fiscal tools to support your financial goals. Our work complements the services of your existing advisors, including CPAs and attorneys. The degree and sophistication of the plan varies according to your circumstances.</p>
  <p class="firm-note">"The Moska House LLC does not provide specific tax or legal advice. Please consult your accountant and/or attorney regarding your specific situation.</p>
  <div class="location location--mpls" role="img" aria-label="Photo of the Minneapolis skyline reflected in a lake"></div>
  <div class="location location--sf" role="img" aria-label="Photo of a domed rotunda beside a lagoon in San Francisco"></div>
  <div class="location__label location__label--mpls">Minneapolis Location</div>
  <div class="location__label location__label--sf">San Francisco Location</div>
  <footer class="page-foot"><span>Copyright @ 2026 KVL Wealth Management</span><span class="page-foot__num">Page Number: <b>03</b></span></footer>
</section>

</body>
</html>
```